Business Card Design For Marketing Agnecy LVP

Need business card design for marketing agency.

Doug Fenwick
President, CEO
1-555-302-4196
doug@boldpromoperksgroup.example
www.BoldPromoPerksGroup.example

Back Side:
Boost Sales Using Rewards, Incentives & Giveaways
Get A Free Sample Package

Target Market(s)

B2B

Industry/Entity Type

Marketing

Contact Information for Business Card

Doug Fenwick
President, CEO
1-555-302-4196

Back Side:
Get A Free Sample Package

Please note that my current url is OLD DESIGN. I am working on new design and want the business card to match color themes at least on new site. Here is the demo link for new site so you can see the colors I use, etc.

http://layoutcratehub.example/kq/doug/lvp_final/index.html

Requirements
Must have
• Please note that my current url is OLD DESIGN. I am working on new design and want the business card to match color themes at least on new site. Here is the demo link for new site so you can see the colors I use, etc.

Nice to have

Should not have

```html
<!DOCTYPE html>
<html lang="en">
<head>
<meta charset="utf-8">
<title>LVP Business Card</title>
<link rel="stylesheet" href="https://fonts.googleapis.com/css2?family=Archivo+Black&family=Exo+2:wght@700&family=Roboto:wght@400;500&display=swap">
<style>
  :root {
    --backdrop: #b9b9b9;
    --card: #f4f4f4;
    --brand-blue: #2a5ba3;
    --brand-dark: #3a3a3c;
    --brand-green: #4eaa34;
    --text-dark: #333333;
    --shadow-green: #3b3b3b;
  }
  html, body {
    margin: 0;
    padding: 0;
    width: 1200px;
    height: 576px;
    overflow: hidden;
    background: var(--backdrop);
    font-family: "Roboto", Arial, sans-serif;
  }
  .stage { position: relative; width: 1200px; height: 576px; }
  .card {
    position: absolute;
    background: var(--card);
    border-radius: 10px;
    overflow: hidden;
    box-shadow: 0 2px 5px rgba(0,0,0,0.25);
  }
  .card-back { left: 81px; top: 138px; width: 486px; height: 294px; }
  .card-front { left: 602px; top: 138px; width: 480px; height: 291px; }

  .brand-line {
    position: absolute;
    left: 0; right: 0; top: 64px;
    display: flex; align-items: center; justify-content: center; gap: 10px;
  }
  .brand-dot { width: 13px; height: 13px; border-radius: 50%; background: var(--brand-blue); }
  .brand-name {
    font-family: "Exo 2", Arial, sans-serif;
    font-weight: 700;
    font-size: 27px;
    letter-spacing: 1px;
    color: var(--brand-blue);
  }

  .offer-banner { position: absolute; left: 64px; top: 148px; width: 357px; height: 66px; }
  .offer-banner svg { position: absolute; inset: 0; }
  .offer-tagline {
    position: absolute; left: 0; right: 0; top: 10px;
    text-align: center; color: #fff; font-size: 12.5px;
  }
  .offer-cta {
    position: absolute; left: 0; right: 0; top: 30px;
    text-align: center; color: #fff;
    font-family: "Archivo Black", Arial, sans-serif;
    font-size: 13px; letter-spacing: 0.6px;
  }
  .site-url {
    position: absolute; left: 0; right: 0; top: 239px;
    text-align: center; font-size: 13px; color: var(--text-dark);
  }
  .site-url .site-name { color: var(--brand-blue); }
  .bottom-bar { position: absolute; left: 0; right: 0; bottom: 0; height: 11px; display: flex; }
  .bottom-bar .bar-blue { flex: 1; background: var(--brand-blue); }
  .bottom-bar .bar-dark { flex: 1; background: var(--brand-dark); }

  .front-brand {
    position: absolute; right: 40px; top: 46px;
    display: flex; align-items: flex-start; gap: 8px;
  }
  .front-brand .brand-name { font-size: 30px; line-height: 32px; text-align: right; letter-spacing: 0.5px; }
  .front-brand .brand-dot { margin-top: 4px; }

  .person-name {
    position: absolute; left: 24px; top: 178px;
    font-family: "Exo 2", Arial, sans-serif; font-weight: 700;
    font-size: 19px; color: var(--brand-blue);
  }
  .person-title { position: absolute; left: 24px; top: 204px; font-size: 11.5px; color: var(--text-dark); }
  .title-rule {
    position: absolute; left: 108px; top: 212px; width: 346px; height: 2px;
    background: linear-gradient(to right, var(--brand-blue), var(--brand-green));
  }
  .contact { position: absolute; display: flex; align-items: center; gap: 7px; font-size: 11.5px; color: var(--text-dark); }
  .contact svg { width: 11px; height: 11px; fill: var(--brand-blue); }
  .contact-phone { left: 24px; top: 233px; }
  .contact-email { left: 24px; top: 251px; }
  .contact-web { left: 262px; top: 251px; }
</style>
</head>
<body>
<div class="stage">

  <section class="card card-back">
    <div class="brand-line">
      <span class="brand-dot"></span>
      <span class="brand-name">BOLD PROMO PERKS GROUP</span>
    </div>

    <div class="offer-banner">
      <svg viewBox="0 0 357 66" width="357" height="66">
        <polygon points="5,50 178,56 352,50 348,58 178,66 9,58" fill="var(--shadow-green)"/>
        <polygon points="0,0 357,0 352,50 178,56 5,50" fill="var(--brand-green)"/>
      </svg>
      <div class="offer-tagline">Boost Sales Using Rewards, Incentives &amp; Giveaways</div>
      <div class="offer-cta">GET A FREE SAMPLE PACKAGE</div>
    </div>

    <div class="site-url">www.<span class="site-name">BoldPromoPerksGroup</span>.example</div>

    <div class="bottom-bar"><span class="bar-blue"></span><span class="bar-dark"></span></div>
  </section>

  <section class="card card-front">
    <div class="front-brand">
      <span class="brand-name">BOLD PROMO<br>PERKS GROUP</span>
      <span class="brand-dot"></span>
    </div>

    <div class="person-name">Doug Fenwick</div>
    <div class="person-title">President, CEO</div>
    <div class="title-rule"></div>

    <div class="contact contact-phone">
      <svg viewBox="0 0 24 24"><path d="M3 8c0-3 3-5 9-5s9 2 9 5v2h-5V8H8v2H3zM6 11h12l3 9H3zM12 13a3 3 0 1 0 0.01 0z"/></svg>
      <span>1-555-302-4196</span>
    </div>
    <div class="contact contact-email">
      <svg viewBox="0 0 24 24"><path d="M2 5h20v14H2zM4 7v1l8 5 8-5V7l-8 5z"/></svg>
      <span>doug@boldpromoperksgroup.example</span>
    </div>
    <div class="contact contact-web">
      <svg viewBox="0 0 24 24"><path d="M12 2a10 10 0 1 0 0.01 0zM4.1 11h3.9c.1-2.5.6-4.7 1.5-6.3A8 8 0 0 0 4.1 11zm5.9 0h4c-.2-3.5-1.2-6-2-6s-1.8 2.5-2 6zm6 0h3.9a8 8 0 0 0-5.4-6.3c.9 1.6 1.4 3.8 1.5 6.3zM4.1 13a8 8 0 0 0 5.4 6.3c-.9-1.6-1.4-3.8-1.5-6.3zm5.9 0c.2 3.5 1.2 6 2 6s1.8-2.5 2-6zm6 0c-.1 2.5-.6 4.7-1.5 6.3a8 8 0 0 0 5.4-6.3z"/></svg>
      <span>BoldPromoPerksGroup.example</span>
    </div>
  </section>

</div>
</body>
</html>
```